Meridale Bed Company Needs Business Card

Looking for a very nice looking business card. Creative but not extravagant. We sell beds and pillows across the U.S. and need something professional but catchy. I have attached the logo.

Name : Devin Holt
Title : President
Phone : (800) 471-2960
Email: sleep@quilmora.com
Website: www.quilmora.com

Can be single-sided or double-sided
horizontal or vertical

Can use Blues/Greys

Target Market(s)

Mass Market

Industry/Entity Type

Retail

Contact Information for Business Card

Name : Devin Holt
Title : President
Phone : (800) 471-2960
Email: sleep@quilmora.com
Website: www.quilmora.com

Requirements
Must have
• Clean, Modern, Smooth
• Can use Blues/Greys
• On the other side without the information - have something simple like www.quilmora.com or our logo
Nice to have
• Surprise me
Should not have
• Nothing crazy, nothing cluttered

```html
<!DOCTYPE html>
<html lang="en">
<head>
<meta charset="utf-8">
<title>Meridale Bed Company – Business Card</title>
<link href="https://fonts.googleapis.com/css2?family=Quicksand:wght@300&family=Montserrat:wght@600&family=Open+Sans:wght@400&display=swap" rel="stylesheet">
<style>
  :root{
    --page:#e8e6e2;
    --brand-blue:#2fa3d8;
    --brand-grey:#9a9a9c;
    --ink-grey:#5a5a5c;
    --card-white:#ffffff;
  }
  html,body{margin:0;padding:0;overflow:hidden;}
  body{
    width:1200px;height:1023px;background:var(--page);
    display:flex;flex-direction:column;align-items:center;justify-content:center;gap:60px;
  }
  .card{width:700px;height:400px;box-shadow:0 6px 18px rgba(0,0,0,.18);display:block;}
  .wordmark{font-family:"Quicksand",sans-serif;font-weight:300;}
  .holder-name{font-family:"Montserrat",sans-serif;font-weight:600;}
  .contact{font-family:"Open Sans",sans-serif;font-weight:400;}
</style>
</head>
<body>

<svg class="card card-front" viewBox="0 0 700 400" xmlns="http://www.w3.org/2000/svg" aria-label="Front of business card">
  <rect width="700" height="400" fill="var(--card-white)"/>

  <!-- top-left swoosh -->
  <path class="band-grey" d="M262,0 H700 V8 H290 C190,40 80,150 14,330 L0,345 V300 C60,150 170,40 262,0 Z" fill="var(--brand-grey)"/>
  <path class="band-blue" d="M0,0 H248 C160,42 60,150 0,292 Z" fill="var(--brand-blue)"/>

  <!-- bottom-right swoosh -->
  <path class="band-grey" d="M230,400 C350,392 420,350 452,290 L470,270 C445,350 380,392 300,400 Z" fill="var(--brand-grey)"/>
  <path class="band-blue" d="M700,130 C560,130 500,190 470,270 C440,350 380,392 296,400 H700 Z" fill="var(--brand-blue)"/>

  <!-- wordmark -->
  <text class="wordmark" x="270" y="262" text-anchor="middle" font-size="88" fill="var(--brand-blue)">quilmora</text>

  <!-- holder -->
  <text class="holder-name" x="640" y="56" text-anchor="end" font-size="20" fill="var(--brand-blue)">Devin Holt</text>
  <text class="contact" x="640" y="77" text-anchor="end" font-size="14" fill="var(--ink-grey)">President</text>
  <rect x="648" y="38" width="20" height="20" rx="4" fill="var(--brand-grey)"/>

  <!-- contacts -->
  <g class="contact" font-size="15" fill="#fff" text-anchor="end">
    <text x="652" y="245">(800) 471-2960</text>
    <text x="652" y="270">sleep@quilmora.com</text>
    <text x="652" y="295">www.quilmora.com</text>
  </g>
  <!-- phone icon -->
  <rect x="660" y="232" width="16" height="16" rx="3" fill="#fff"/>
  <path d="M664,236 q1,6 7,8 l1,-2 -2,-1 -1,1 q-2,-1 -3,-3 l1,-1 -1,-2 z" fill="var(--brand-blue)"/>
  <!-- mail icon -->
  <rect x="660" y="257" width="16" height="16" rx="3" fill="#fff"/>
  <path d="M663,261 h10 v8 h-10 z M663,261 l5,4 5,-4" fill="none" stroke="var(--brand-blue)" stroke-width="1.2"/>
  <!-- globe icon -->
  <rect x="660" y="282" width="16" height="16" rx="3" fill="#fff"/>
  <circle cx="668" cy="290" r="5" fill="none" stroke="var(--brand-blue)" stroke-width="1.2"/>
  <path d="M663,290 h10 M668,285 v10" stroke="var(--brand-blue)" stroke-width="1"/>
</svg>

<svg class="card card-back" viewBox="0 0 700 400" xmlns="http://www.w3.org/2000/svg" aria-label="Back of business card">
  <rect width="700" height="400" fill="var(--brand-blue)"/>
  <text class="wordmark" x="350" y="232" text-anchor="middle" font-size="96" fill="#fff">quilmora</text>
</svg>

</body>
</html>
```